Business Cards Design for the electrical wholesaler: clean bold dynamic :)

We need a business card design that would follow our latest brand guidelines. As an electrical wholesaler we want to bring a fresh look and feel into the industry. The design should be clean bold and dynamic. It should come alive with the renewed energy of our green colour. Our grey colour should keep things balanced and complement the notion of maturity and responsibility. We employ Lato as a corporate font however are not bound by this font and we’re open to interpretation here.

Target Market(s)

Electrical contractors

Industry/Entity Type

Business

Contact Information for Business Card

Logo
Name & Surname: Halyna Dorosh
Job Title: Director of Marketing
Email: halya.dorosh@quillmail.example
Cell phone: XXX.XXX.XXXX
Address: 20517 - 87 Ave. Edmonton, AB, Canada. T6K 4N8
Business Phone: 780.555.0184
Website: www.brovix.example

Font styles to use
Other font styles liked:
• Lato

Requirements
Must have
• Logo & website
Nice to have
• Brand elements - some of them you may find in the attached Brand Guidelines (e.g. three lines on the background signifying "W")

```html
<!DOCTYPE html>
<html lang="en">
<head>
<meta charset="utf-8">
<title>Brovix business card</title>
<link rel="stylesheet" href="https://fonts.googleapis.com/css2?family=Lato:wght@400;700&display=swap">
<style>
  :root {
    --backdrop: #b9b9b9;
    --graphite: #464a4d;
    --graphite-soft: #505458;
    --paper: #f3f3f3;
    --green: #6ab023;
    --ink: #3f4346;
    --white: #ffffff;
  }
  * { margin: 0; padding: 0; box-sizing: border-box; }
  html, body {
    width: 1200px; height: 576px; overflow: hidden;
    background: var(--backdrop);
    font-family: "Lato", sans-serif;
  }
  .card {
    position: absolute; top: 138px;
    width: 484px; height: 294px;
    border-radius: 12px; overflow: hidden;
    box-shadow: 0 2px 4px rgba(0,0,0,.18);
  }
  .card--front { left: 82px; background: var(--graphite); }
  .card--back { left: 602px; background: var(--paper); }

  .brand { position: absolute; display: flex; align-items: center; gap: 8px; }
  .brand__mark { display: block; background: var(--green); }
  .brand__name { font-weight: 400; line-height: 1; }

  .card--front .brand { left: 50%; top: 50%; transform: translate(-50%, -50%); }
  .card--front .brand__mark { width: 26px; height: 26px; }
  .card--front .brand__name { font-size: 46px; color: var(--white); }

  .card--back .brand { left: 22px; top: 30px; }
  .card--back .brand__mark { width: 18px; height: 18px; }
  .card--back .brand__name { font-size: 32px; color: var(--ink); }

  .accent-block {
    position: absolute; left: 300px; top: 46px;
    width: 130px; height: 248px; background: var(--graphite);
  }
  .accent-band {
    position: absolute; right: 0; top: 0;
    width: 30px; height: 100%; background: var(--green);
  }

  .contact { position: absolute; left: 24px; top: 128px; color: var(--ink); }
  .contact__name { font-size: 21px; font-weight: 700; color: var(--green); line-height: 1.1; }
  .contact__role { font-size: 12px; margin-top: 4px; }
  .contact__address { font-size: 12px; line-height: 16px; margin-top: 14px; }
  .contact__list { list-style: none; margin-top: 12px; font-size: 12px; }
  .contact__item { display: flex; align-items: center; gap: 8px; height: 16.5px; }
  .contact__icon { width: 11px; height: 11px; flex: none; }
</style>
</head>
<body>
  <section class="card card--front">
    <div class="brand">
      <span class="brand__mark"></span>
      <span class="brand__name">brovix</span>
    </div>
  </section>

  <section class="card card--back">
    <div class="accent-block"></div>
    <div class="accent-band"></div>
    <div class="brand">
      <span class="brand__mark"></span>
      <span class="brand__name">brovix</span>
    </div>
    <div class="contact">
      <p class="contact__name">Halyna Dorosh</p>
      <p class="contact__role">Founder &amp; CEO</p>
      <p class="contact__address">20517 - 87 Ave. Edmonton,<br>AB, Canada T6K 4N8</p>
      <ul class="contact__list">
        <li class="contact__item">
          <svg class="contact__icon" viewBox="0 0 12 12"><circle cx="6" cy="6" r="6" fill="#6ab023"/><path d="M3.6 3.3c.3-.3.7-.3.9 0l.7.9c.2.3.1.6-.1.8l-.3.3c.4.8 1 1.4 1.8 1.8l.3-.3c.2-.2.5-.3.8-.1l.9.7c.3.2.3.6 0 .9l-.4.4c-.4.4-1 .4-1.5.2-1.6-.7-2.8-1.9-3.5-3.5-.2-.5-.2-1.1.2-1.5z" fill="#fff"/></svg>
          <span>+1 780-555-0184</span>
        </li>
        <li class="contact__item">
          <svg class="contact__icon" viewBox="0 0 12 12"><circle cx="6" cy="6" r="6" fill="#6ab023"/><rect x="3" y="4" width="6" height="4.2" fill="none" stroke="#fff" stroke-width=".9"/><path d="M3 4l3 2.3L9 4" fill="none" stroke="#fff" stroke-width=".9"/></svg>
          <span>halya.dorosh@quillmail.example</span>
        </li>
        <li class="contact__item">
          <svg class="contact__icon" viewBox="0 0 12 12"><circle cx="6" cy="6" r="6" fill="#6ab023"/><circle cx="6" cy="6" r="3" fill="none" stroke="#fff" stroke-width=".8"/><path d="M3 6h6M6 3c-1.3 1.6-1.3 4.4 0 6M6 3c1.3 1.6 1.3 4.4 0 6" fill="none" stroke="#fff" stroke-width=".7"/></svg>
          <span>www.brovix.example</span>
        </li>
      </ul>
    </div>
  </section>
</body>
</html>
```